Gymnastics Schedule for our Junior Gymnastics program (for pre-school aged children)

We are wanting an updated version of our timetable for our Junior Gym program, I have attached a link to our website to align with branding, I have attached an old timetable as an example and our avatars we want to use. https://tlr.org.au/
Target Market(s)
We have created an avatar to give you an idea of target market: Maren Holt- a 32 year old married mother of 2. she has a 4 year old and a 1 year old. she is a small business owner who works from home. She values learning and prgoression for her children in gymnastics as well as socialization, activeness and providing the best opportunities.
Industry/Entity Type
Children's Sport - Gymnastics
Font styles to use
Other font styles liked:
- Franklin Gothic
Look and feel

```html
<!DOCTYPE html>
<html lang="en">
<head>
<meta charset="utf-8">
<title>Larchmont Gymnastics Centre – 2025 Junior Gymnastics Timetable</title>
<link rel="stylesheet" href="https://fonts.googleapis.com/css2?family=Libre+Franklin:wght@700;800;900&family=Varela+Round&family=Outfit:wght@400&family=Delius&display=swap">
<style>
  :root {
    --navy: #10128a;
    --red: #e8262d;
    --white: #ffffff;
    --skin: #e9c9a0;
    --tan: #b59a7c;
    --sky: #6b8fd6;
    --gold: #c5a54a;
  }
  * { margin: 0; padding: 0; box-sizing: border-box; }
  html, body { width: 1200px; height: 848px; overflow: hidden; background: var(--white); }
  .sheet { position: relative; width: 1200px; height: 848px; font-family: "Outfit", sans-serif; color: var(--navy); }

  .centre-name { position: absolute; left: 45px; top: 46px; font: 800 28px/1 "Libre Franklin", sans-serif; color: var(--red); white-space: nowrap; }
  .year { position: absolute; left: 500px; top: 34px; font: 900 58px/1 "Libre Franklin", sans-serif; color: var(--navy); }
  .title { position: absolute; left: 44px; top: 92px; font: 900 53px/1 "Libre Franklin", sans-serif; color: var(--navy); white-space: nowrap; }

  .partner { position: absolute; display: flex; flex-direction: column; align-items: center; gap: 5px; font: 800 12px/1.15 "Libre Franklin", sans-serif; color: var(--navy); text-align: center; }
  .partner .mark { width: 44px; height: 44px; border-radius: 50%; background: var(--navy); flex: none; }
  .partner--club { left: 700px; top: 42px; width: 126px; font-size: 15px; }
  .partner--club .mark { background: var(--red); width: 30px; height: 30px; }
  .partner--state { left: 840px; top: 40px; width: 86px; }
  .badge { position: absolute; left: 948px; top: 46px; width: 54px; height: 64px; border-radius: 8px; background: var(--gold); opacity: .85; }

  .timetable { position: absolute; left: 46px; top: 180px; width: 828px; border-collapse: collapse; table-layout: fixed; }
  .timetable th { height: 40px; font: 800 19px "Libre Franklin", sans-serif; color: var(--red); border-top: 3px solid var(--navy); border-bottom: 3px solid var(--navy); }
  .timetable td { height: 32px; text-align: center; font: 14px "Varela Round", sans-serif; color: var(--navy); border-bottom: 1.5px solid var(--navy); white-space: nowrap; }
  .timetable th + th, .timetable td + td { border-left: 2px solid var(--navy); }
  .timetable col.day { width: 168px; }
  .timetable col.sun { width: 156px; }

  .section-banner { position: absolute; left: 39px; top: 509px; width: 285px; height: 43px; background: var(--navy); color: var(--white); font: 800 22px/43px "Libre Franklin", sans-serif; text-align: center; transform: rotate(-0.3deg); }

  .program-points { position: absolute; left: 42px; top: 566px; list-style: none; font-size: 17px; line-height: 21px; }
  .program-points li { position: relative; padding-left: 30px; margin-bottom: 9.5px; }
  .program-points li svg { position: absolute; left: 0; top: 3px; }

  .tagline { position: absolute; left: 42px; top: 788px; font: 21px "Delius", sans-serif; color: var(--navy); white-space: nowrap; }

  .art { position: absolute; border-radius: 24px; }
  .art--top { left: 1030px; top: 0; width: 170px; height: 175px; background: linear-gradient(160deg, var(--sky), var(--skin)); }
  .art--leap { left: 892px; top: 176px; width: 272px; height: 226px; background: linear-gradient(140deg, var(--tan), #d8a49a 60%, #b8c4ea); }
  .art--sparkle { left: 925px; top: 414px; width: 96px; height: 120px; background: linear-gradient(120deg, #dfe3f6, #c7cdf0); }
  .art--sparkle-small { left: 756px; top: 528px; width: 80px; height: 78px; background: linear-gradient(120deg, #dfe3f6, #c7cdf0); }
  .art--split { left: 802px; top: 564px; width: 250px; height: 192px; background: linear-gradient(160deg, var(--skin), #d46a62 70%, var(--sky)); }
  .art--handstand { left: 1052px; top: 414px; width: 114px; height: 302px; background: linear-gradient(180deg, var(--sky), var(--tan)); }
  .art--stars { left: 976px; top: 742px; width: 206px; height: 96px; background: linear-gradient(90deg, #f3c9cb, #c7cdf0); }
</style>
</head>
<body>
<main class="sheet">
  <h2 class="centre-name">Larchmont Gymnastics Centre</h2>
  <div class="year">2025</div>
  <h1 class="title">JUNIOR GYMNASTICS</h1>

  <div class="partner partner--club"><span class="mark"></span>LARCHMONT<br>Gymnastics Centre</div>
  <div class="partner partner--state"><span class="mark"></span>Stateline Gym Council</div>
  <div class="badge" role="img" aria-label="Accreditation badge"></div>

  <table class="timetable">
    <colgroup><col class="day"><col class="day"><col class="day"><col class="day"><col class="sun"></colgroup>
    <thead><tr><th>MONDAY</th><th>WEDNESDAY</th><th>THURSDAY</th><th>FRIDAY</th><th>SUNDAY</th></tr></thead>
    <tbody>
      <tr><td>9.30am - 10.20am</td><td>9.30am - 10.20am</td><td>9.30am - 10.20am</td><td>9.30am - 10.20am</td><td>9.00am - 9.50am</td></tr>
      <tr><td>10.30am - 11.20am</td><td>10.30am - 11.20am</td><td>10.30am - 11.20am</td><td>10.30am - 11.20am</td><td>9.15am - 10.05am</td></tr>
      <tr><td>11.30am - 12.20pm</td><td>11.30am - 12.20pm</td><td>11.30am - 12.20pm</td><td>11.30am - 12.20pm</td><td>10.00am - 10.50am</td></tr>
      <tr><td>2.00pm - 2.50pm</td><td>2.00pm - 2.50pm</td><td>2.00pm - 2.50pm</td><td>2.00pm - 2.50pm</td><td>10.15am - 11.05am</td></tr>
      <tr><td></td><td></td><td></td><td></td><td>11.00am - 11.50am</td></tr>
      <tr><td></td><td></td><td></td><td></td><td>11.15am - 12.05pm</td></tr>
      <tr><td></td><td></td><td></td><td></td><td>12.00pm - 12.50pm</td></tr>
      <tr><td></td><td></td><td></td><td></td><td>12.15pm - 1.05pm</td></tr>
    </tbody>
  </table>

  <div class="section-banner">ABOUT OUR PROGRAM</div>

  <ul class="program-points">
    <li><svg width="16" height="16" viewBox="0 0 16 16"><rect x="1" y="3" width="12" height="12" fill="none" stroke="#e8262d" stroke-width="2"/><path d="M4 8l3 3 8-9" fill="none" stroke="#e8262d" stroke-width="2"/></svg>Larchmont Gymnastics is a 5-star Centre, as rated by National Gym Federation</li>
    <li><svg width="16" height="16" viewBox="0 0 16 16"><rect x="1" y="3" width="12" height="12" fill="none" stroke="#e8262d" stroke-width="2"/><path d="M4 8l3 3 8-9" fill="none" stroke="#e8262d" stroke-width="2"/></svg>Junior Gym is a structured program with an emphasis on fun and learning –<br>a program that grows with your child!</li>
    <li><svg width="16" height="16" viewBox="0 0 16 16"><rect x="1" y="3" width="12" height="12" fill="none" stroke="#e8262d" stroke-width="2"/><path d="M4 8l3 3 8-9" fill="none" stroke="#e8262d" stroke-width="2"/></svg>We teach gymnastics skills that can lead to improved co-ordination, balance and confidence</li>
    <li><svg width="16" height="16" viewBox="0 0 16 16"><rect x="1" y="3" width="12" height="12" fill="none" stroke="#e8262d" stroke-width="2"/><path d="M4 8l3 3 8-9" fill="none" stroke="#e8262d" stroke-width="2"/></svg>Suitable for children aged 2-5 years old (not yet attending school)</li>
    <li><svg width="16" height="16" viewBox="0 0 16 16"><rect x="1" y="3" width="12" height="12" fill="none" stroke="#e8262d" stroke-width="2"/><path d="M4 8l3 3 8-9" fill="none" stroke="#e8262d" stroke-width="2"/></svg>Parent assisted classes for 2-4 year olds, and non parent assisted classes for 4-5 year olds</li>
    <li><svg width="16" height="16" viewBox="0 0 16 16"><rect x="1" y="3" width="12" height="12" fill="none" stroke="#e8262d" stroke-width="2"/><path d="M4 8l3 3 8-9" fill="none" stroke="#e8262d" stroke-width="2"/></svg>All classes are led by our warm, friendly and qualified coaches and run for 50 minutes</li>
  </ul>

  <p class="tagline">Larchmont's Junior Gym Program - Fun, Safe, Learning - A program that grows with your child</p>

  <div class="art art--top" role="img" aria-label="Illustrated child in a striped leotard hanging upside down"></div>
  <div class="art art--leap" role="img" aria-label="Illustrated girl in a leotard leaping with a shooting star"></div>
  <div class="art art--sparkle" role="img" aria-label="Hand-drawn sparkles"></div>
  <div class="art art--sparkle-small" role="img" aria-label="Hand-drawn small stars"></div>
  <div class="art art--handstand" role="img" aria-label="Illustrated child doing a handstand"></div>
  <div class="art art--split" role="img" aria-label="Illustrated girl doing the splits"></div>
  <div class="art art--stars" role="img" aria-label="Hand-drawn red and navy stars"></div>
</main>
</body>
</html>
```